Business Cards Design for the electrical wholesaler: clean bold dynamic :)

We need a business card design that would follow our latest brand guidelines. As an electrical wholesaler we want to bring a fresh look and feel into the industry. The design should be clean bold and dynamic. It should come alive with the renewed energy of our green colour. Our grey colour should keep things balanced and complement the notion of maturity and responsibility. We employ Lato as a corporate font however are not bound by this font and we’re open to interpretation here.

Target Market(s)

Electrical contractors

Industry/Entity Type

Business

Contact Information for Business Card

Logo
Name & Surname: Halyna Dorosh
Job Title: Director of Marketing
Email: halya.dorosh@quillmail.example
Cell phone: XXX.XXX.XXXX
Address: 20517 - 87 Ave. Edmonton, AB, Canada. T6K 4N8
Business Phone: 780.555.0184
Website: www.brovix.example

Font styles to use
Other font styles liked:
• Lato

Requirements
Must have
• Logo & website
Nice to have
• Brand elements - some of them you may find in the attached Brand Guidelines (e.g. three lines on the background signifying "W")

```html
<!DOCTYPE html>
<html lang="en">
<head>
<meta charset="utf-8">
<title>Brovix Business Card</title>
<link rel="stylesheet" href="https://fonts.googleapis.com/css2?family=Exo+2:wght@600&family=Lato:wght@400;700&display=swap">
<style>
  :root {
    --backdrop: #3b3b3d;
    --card: #1c1c1e;
    --card-edge: #2a2a2c;
    --green: #8ccf3a;
    --grey: #b9b9bb;
    --grey-dark: #4a4a4d;
    --white: #f2f2f2;
  }
  * { margin: 0; padding: 0; box-sizing: border-box; }
  html, body { width: 799px; height: 1200px; overflow: hidden; }
  body {
    background: var(--backdrop);
    font-family: "Lato", sans-serif;
    position: relative;
  }
  .card {
    position: absolute;
    left: 70px;
    width: 660px;
    height: 378px;
    background: var(--card);
    border: 1px solid var(--card-edge);
    border-radius: 26px;
    overflow: hidden;
  }
  .card--front { top: 160px; }
  .card--back { top: 670px; }

  .front-brand {
    position: absolute;
    left: 0; right: 0; top: 150px;
    font-family: "Lato", sans-serif;
    font-weight: 700;
    font-size: 88px;
    letter-spacing: 1px;
    color: var(--grey-dark);
    display: flex;
    justify-content: center;
    align-items: center;
    gap: 22px;
  }
  .front-brand .mark {
    width: 60px; height: 60px;
    background: var(--grey-dark);
    border-radius: 6px;
  }

  .back-brand {
    position: absolute;
    left: 44px; top: 150px;
    display: flex;
    align-items: center;
    gap: 12px;
  }
  .back-brand .mark {
    width: 42px; height: 42px;
    background: var(--green);
    border-radius: 4px;
  }
  .back-brand .name {
    font-family: "Lato", sans-serif;
    font-weight: 700;
    font-size: 54px;
    color: var(--grey);
  }

  .contact {
    position: absolute;
    left: 320px; top: 100px;
    width: 320px;
    color: var(--white);
    font-size: 16px;
    line-height: 1.35;
  }
  .contact .person {
    font-family: "Exo 2", sans-serif;
    font-weight: 600;
    font-size: 30px;
    color: var(--green);
    line-height: 1.1;
  }
  .contact .role { font-size: 16px; margin-bottom: 12px; }
  .contact .address { margin-bottom: 8px; }
  .contact .line { display: flex; align-items: center; gap: 8px; white-space: nowrap; }
  .icon { width: 16px; height: 16px; flex: none; }
</style>
</head>
<body>
  <section class="card card--front">
    <div class="front-brand"><span class="mark"></span><span>brovix</span></div>
  </section>

  <section class="card card--back">
    <div class="back-brand"><span class="mark"></span><span class="name">brovix</span></div>

    <div class="contact">
      <p class="person">Halyna Dorosh</p>
      <p class="role">Director of Marketing</p>
      <p class="address">20517 - 87 Ave. Edmonton,<br>AB, Canada T6K 4N8</p>
      <p class="line">
        <svg class="icon" viewBox="0 0 16 16"><circle cx="8" cy="8" r="8" fill="#8ccf3a"/><path d="M5 4.5c.5-.5 1.2-.5 1.5 0l.8 1.3c.2.4 0 .8-.3 1l-.5.4c.4.9 1.1 1.6 2 2l.4-.5c.3-.3.7-.4 1-.2l1.3.8c.5.3.5 1 0 1.5-.7.7-1.8.8-2.8.2A8 8 0 0 1 4.8 7.3c-.6-1-.5-2.1.2-2.8z" fill="#1c1c1e"/></svg>
        +1 780-555-0184
      </p>
      <p class="line">
        <svg class="icon" viewBox="0 0 16 16"><circle cx="8" cy="8" r="8" fill="#8ccf3a"/><rect x="4" y="5" width="8" height="6" rx="1" fill="#1c1c1e"/><path d="M4.5 5.5 8 8.5l3.5-3" stroke="#8ccf3a" fill="none" stroke-width="1"/></svg>
        halya.dorosh@quillmail.example
      </p>
      <p class="line">
        <svg class="icon" viewBox="0 0 16 16"><circle cx="8" cy="8" r="8" fill="#8ccf3a"/><circle cx="8" cy="8" r="4.5" fill="none" stroke="#1c1c1e" stroke-width="1.2"/><path d="M3.5 8h9M8 3.5c-2 2.5-2 6.5 0 9M8 3.5c2 2.5 2 6.5 0 9" stroke="#1c1c1e" fill="none" stroke-width="1"/></svg>
        brovix.example
      </p>
    </div>
  </section>
</body>
</html>
```